Business Card for Coastal Tundrabridge Advisory

We need a business card for Coastal Tundrabridge Advisory. The company website address is provided below. The company logo is attached. We provide specialized permafrost services to the mining, transportation, and oil & gas industries. The card should be prepared for:
Matthias Korhonen, PhD.
Coastal Tundrabridge Advisory
PO Box 418259
Quillwater, Alaska 99642
Direct: +1-907-555-0143
Email: mkorhonen@tundrabridgeadvisory.example
Website: www.coastaltundrabridgeadvisory.example

```html
<!DOCTYPE html>
<html lang="en">
<head>
<meta charset="utf-8">
<title>Coastal Tundrabridge Advisory — Business Card</title>
<link rel="stylesheet" href="https://fonts.googleapis.com/css2?family=Montserrat:wght@400;600;700&display=swap">
<style>
  :root {
    --backdrop: #e4e1dc;
    --card: #ffffff;
    --ink: #1c2228;
    --band-dark: #333335;
    --band-grey: #6b6b6b;
    --band-text: #ffffff;
  }
  * { margin: 0; padding: 0; box-sizing: border-box; }
  html, body {
    width: 900px; height: 1200px; overflow: hidden;
    background: var(--backdrop);
    font-family: "Montserrat", Arial, sans-serif;
    color: var(--ink);
  }
  .canvas { position: relative; width: 900px; height: 1200px; }
  .card {
    position: absolute; left: 80px; width: 742px; height: 440px;
    background: var(--card); border-radius: 40px; overflow: hidden;
  }
  .card--front { top: 132px; }
  .card--back { top: 638px; }

  .company-name {
    font-weight: 700; text-transform: uppercase; color: var(--ink);
    letter-spacing: 2px; line-height: 1.15;
  }
  .card--front .company-name {
    position: absolute; left: 55px; top: 48px; font-size: 32px;
  }
  .card--back .company-name {
    position: absolute; left: 0; right: 0; top: 172px;
    text-align: center; font-size: 38px;
  }

  .person { position: absolute; left: 38px; top: 236px; }
  .person__name { font-weight: 700; font-size: 26px; line-height: 1.2; }
  .person__title { font-weight: 400; font-size: 16px; margin-top: 2px; }

  .band { position: absolute; left: 0; top: 301px; width: 742px; height: 103px; }
  .contact-list {
    position: absolute; left: 44px; top: 320px; list-style: none;
    color: var(--band-text); font-size: 15.5px; line-height: 22.5px;
  }
  .contact-list li { display: flex; align-items: center; gap: 10px; }
  .contact-list svg { width: 14px; height: 14px; flex: none; }
  .address {
    position: absolute; left: 518px; top: 350px;
    color: var(--band-text); font-size: 16px; line-height: 21px; font-style: normal;
  }
  .back-strip {
    position: absolute; left: 0; bottom: 0; width: 100%; height: 16px;
    background: var(--band-dark);
  }
</style>
</head>
<body>
<main class="canvas">
  <section class="card card--front">
    <div class="company-name">Coastal Tundrabridge<br>Advisory</div>

    <div class="person">
      <div class="person__name">Matthias Korhonen, PhD.</div>
      <div class="person__title">CEO &amp; Founder</div>
    </div>

    <svg class="band" viewBox="0 0 742 103" aria-hidden="true">
      <polygon points="0,0 508,0 458,103 0,103" fill="var(--band-dark)"/>
      <polygon points="520,0 742,0 742,103 468,103" fill="var(--band-grey)"/>
    </svg>

    <ul class="contact-list">
      <li>
        <svg viewBox="0 0 14 14" aria-hidden="true"><path d="M1 5 Q7 1 13 5 L11 7 L9 5.5 L5 5.5 L3 7 Z M3 8 H11 L12 12 H2 Z" fill="#fff"/></svg>
        +1-907-555-0143
      </li>
      <li>
        <svg viewBox="0 0 14 14" aria-hidden="true"><rect x="1" y="3" width="12" height="8" fill="#fff"/><path d="M1 3 L7 8 L13 3" stroke="var(--band-dark)" stroke-width="1.2" fill="none"/></svg>
        mkorhonen@tundrabridgeadvisory.example
      </li>
      <li>
        <svg viewBox="0 0 14 14" aria-hidden="true"><circle cx="7" cy="7" r="6" fill="#fff"/><path d="M4 4 Q6 6 5 9 M9 3 Q8 6 10 10" stroke="var(--band-dark)" stroke-width="1.3" fill="none"/></svg>
        www.coastaltundrabridgeadvisory.example
      </li>
    </ul>

    <address class="address">PO Box 418259<br>Quillwater, Alaska 99642</address>
  </section>

  <section class="card card--back">
    <div class="company-name">Coastal Tundrabridge<br>Advisory</div>
    <div class="back-strip"></div>
  </section>
</main>
</body>
</html>
```